Looking for someone to design a business card for my plumbing business Quandor Plumbing Solutions I want the background also to be black, must attract clients. If possible I want the front to be the logo and the back to show maybe the details.

Target Market(s)

Clients

Industry/Entity Type

Plumbing maintenance

Contact Information for Business Card

Name: Felix, Contact: 0461 539 207, Email: quandorplumbingsolutions@mailbrook.example, Licence number 728093K

Font styles to use
Other font styles liked:
• as per logo maybe?

Colors

Designer to choose colors to be used in the design.

Requirements
Nice to have
• stating the service I provide, emergency plumbing, plumbing maintenance, drainage maintenance, block sewer and stormwater, camera and locating.

```html
<!DOCTYPE html>
<html lang="en">
<head>
<meta charset="utf-8">
<title>Quandor Plumbing Solutions – Business Card</title>
<link href="https://fonts.googleapis.com/css2?family=Montserrat:wght@400;500;700;800&display=swap" rel="stylesheet">
<style>
  :root {
    --backdrop: #141414;
    --card: #232324;
    --card-edge: #2a2a2b;
    --blue: #4a8fd1;
    --white: #f2f2f2;
    --text: #e6e6e6;
    --mark-dim: #4b4b4d;
  }
  * { margin: 0; padding: 0; box-sizing: border-box; }
  html, body {
    width: 1200px; height: 1059px; overflow: hidden;
    background: var(--backdrop);
    font-family: "Montserrat", sans-serif;
  }
  .canvas { position: relative; width: 1200px; height: 1059px; }
  .card {
    position: absolute;
    background: var(--card);
    border-radius: 20px;
    box-shadow: 0 8px 24px rgba(0,0,0,0.55);
    overflow: hidden;
  }
  .card--front { left: 257px; top: 89px; width: 687px; height: 390px; }
  .card--back  { left: 254px; top: 547px; width: 693px; height: 393px; }

  /* front */
  .brand {
    position: absolute; left: 38px; top: 52px;
    display: flex; align-items: center; gap: 12px;
  }
  .brand__dot { width: 26px; height: 26px; border-radius: 50%; background: var(--blue); }
  .brand__name {
    color: var(--white); font-weight: 800; font-size: 25px;
    line-height: 1.05; text-transform: uppercase; letter-spacing: 0.5px;
  }
  .accent-bar {
    position: absolute; left: 0; top: 199px; width: 16px; height: 35px;
    background: var(--blue);
  }
  .person { position: absolute; left: 39px; top: 195px; }
  .person__name { color: var(--blue); font-weight: 700; font-size: 26px; line-height: 1; letter-spacing: 0.3px; }
  .person__role { color: var(--text); font-size: 16px; margin-top: 2px; }
  .licence { position: absolute; left: 39px; top: 252px; color: var(--text); font-size: 16px; }
  .contacts { position: absolute; left: 39px; top: 284px; list-style: none; }
  .contacts li {
    display: flex; align-items: center; gap: 8px;
    color: var(--text); font-size: 16px; height: 26px;
  }
  .contacts svg { width: 13px; height: 13px; flex: none; }

  /* back */
  .back-brand {
    position: absolute; left: 0; right: 0; top: 150px;
    display: flex; justify-content: center; align-items: center; gap: 16px;
  }
  .back-brand__dot { width: 34px; height: 34px; border-radius: 50%; background: var(--blue); }
  .back-brand__name {
    color: var(--mark-dim); font-weight: 800; font-size: 38px;
    line-height: 1.05; text-transform: uppercase;
  }
  .services {
    position: absolute; left: 0; right: 0; top: 308px;
    text-align: center; color: var(--text); font-size: 15.5px; line-height: 28px;
  }
  .services .sep { color: var(--blue); margin: 0 6px; }
</style>
</head>
<body>
<div class="canvas">

  <section class="card card--front">
    <div class="brand">
      <span class="brand__dot"></span>
      <span class="brand__name">Quandor<br>Plumbing Solutions</span>
    </div>

    <span class="accent-bar"></span>
    <div class="person">
      <div class="person__name">FELIX</div>
      <div class="person__role">Founder &amp; CEO</div>
    </div>
    <div class="licence">Licence number 728093K</div>

    <ul class="contacts">
      <li>
        <svg viewBox="0 0 24 24" aria-hidden="true"><path fill="#4a8fd1" d="M6.6 10.8a15.1 15.1 0 0 0 6.6 6.6l2.2-2.2a1 1 0 0 1 1-.25 11.4 11.4 0 0 0 3.6.57 1 1 0 0 1 1 1V20a1 1 0 0 1-1 1A17 17 0 0 1 3 4a1 1 0 0 1 1-1h3.5a1 1 0 0 1 1 1c0 1.25.2 2.45.57 3.57a1 1 0 0 1-.25 1z"/></svg>
        0461 539 207
      </li>
      <li>
        <svg viewBox="0 0 24 24" aria-hidden="true"><rect x="1" y="4" width="22" height="16" fill="#4a8fd1"/><path d="M1 4l11 9 11-9" fill="none" stroke="#232324" stroke-width="2"/></svg>
        quandorplumbingsolutions@mailbrook.example
      </li>
      <li>
        <svg viewBox="0 0 24 24" aria-hidden="true"><circle cx="12" cy="12" r="11" fill="#4a8fd1"/></svg>
        @QuandorPlumbingSolutions
      </li>
    </ul>
  </section>

  <section class="card card--back">
    <div class="back-brand">
      <span class="back-brand__dot"></span>
      <span class="back-brand__name">Quandor<br>Plumbing Solutions</span>
    </div>
    <p class="services">
      Emergency plumbing<span class="sep">•</span>Plumbing maintenance<span class="sep">•</span>Drainage maintenance<br>
      Block sewer and stormwater<span class="sep">•</span>Camera and locating
    </p>
  </section>

</div>
</body>
</html>
```